QuillVane needs a dashboard page designed

Redesign the dashboard shown in the provided images.

There are two images:
- dashboard.png
- dashboard-expanded.png

NOTE: The vocabulary navigation on the left will be a very long list of words 100s, so keep that in mind when you're designing both the vocab navigation and the expanded vocab popup.

In the dashboard.png picture, there needs to be a progress chart showing the word progress like the following: review 1(show it as completed) -> review 2(show the user they are here) -> review 3(unvisited) -> review 4(unvisited)

The do-not-design-this-page.png image is for your reference only. It is not to be designed. Use it to understand the overall look and feel of the website to help you create the best dashboard page possible.
Updates

Need extra days to review

Industry/Entity Type

Education English learning

Number of Pages Required

1 page

Requirements
Must have
• The main navigation and main header cannot change between pages. See the do-not-design page for the main navigateion and header.
Should not have
• Do not add a person profile. We will not have images of our users. Keep the icons in the main navigation as they are.

```html
<!DOCTYPE html>
<html lang="en">
<head>
<meta charset="utf-8">
<title>QuillVane Dashboard</title>
<link href="https://fonts.googleapis.com/css2?family=Lato:wght@400;700&display=swap" rel="stylesheet">
<style>
:root{
  --sidebar:#151c27;
  --sidebar-text:#8d939c;
  --sidebar-sub:#6f757e;
  --active-band:#1e3a66;
  --active-text:#8797b4;
  --page:#858585;
  --header-line:#777;
  --card:#8c8c8c;
  --ink:#1b1b1b;
  --body:#3a3a3a;
  --bar:#1c3a6b;
  --modal:#ffffff;
  --modal-ink:#1f1f1f;
  --modal-muted:#7a7a7a;
  --accent-red:#e0191a;
  --star:#c9a116;
}
*{box-sizing:border-box;margin:0;padding:0}
html,body{width:1200px;height:792px;overflow:hidden}
body{font-family:"Lato",sans-serif;background:var(--page);position:relative}
.sidebar{position:absolute;left:0;top:0;width:256px;height:792px;background:var(--sidebar);color:var(--sidebar-text)}
.avatar{position:absolute;left:84px;top:40px}
.user-name{position:absolute;top:140px;width:256px;text-align:center;font-size:17px}
.user-mail{position:absolute;top:164px;width:256px;text-align:center;font-size:13.5px}
.nav{position:absolute;top:204px;left:0;width:256px;list-style:none}
.nav-item{height:32px;display:flex;align-items:center;padding-left:91px;font-size:15.5px;position:relative}
.nav-item svg{position:absolute;left:50px}
.nav-item.active{background:var(--active-band);color:var(--active-text);width:227px;border-radius:0 16px 16px 0;height:32px;margin:4px 0}
.sub{list-style:none;padding:10px 0 6px 91px;font-size:13px;color:var(--sidebar-sub)}
.sub li{height:21.4px}
.header{position:absolute;left:256px;top:0;width:944px;height:42px;border-bottom:1px solid var(--header-line)}
.brand{position:absolute;left:24px;top:13px;font-size:16px;color:var(--ink)}
.word-title{position:absolute;left:386px;top:11px;font-size:18px;font-weight:700;color:var(--ink)}
.card{position:absolute;top:66px;height:77px;background:var(--card);border-radius:3px}
.card.current{border-top:2px solid var(--bar)}
.card-label{position:absolute;left:40px;top:18px;font-size:17px;color:#444}
.card-bar{position:absolute;left:40px;right:24px;top:50px;height:8px;border-radius:4px;background:#777}
.intro{position:absolute;left:284px;top:180px;width:860px;font-size:15.5px;line-height:27.5px;color:var(--body)}
.section-title{position:absolute;left:284px;font-size:17.5px;font-weight:700;color:var(--ink)}
.analysis{position:absolute;left:284px;top:644px;width:860px;font-size:15.5px;line-height:27.5px;color:var(--body)}
.chart{position:absolute;left:0;top:0}
.axis-title{position:absolute;left:711px;top:569px;font-size:15px;color:var(--ink)}
.modal{position:absolute;left:290px;top:75px;width:708px;height:291px;background:var(--modal);border-radius:17px;color:var(--modal-ink)}
.filter{position:absolute;left:38px;top:32px;width:90px;height:29px;border-radius:15px;box-shadow:0 1px 4px rgba(0,0,0,.25);font-size:13px;display:flex;align-items:center;padding-left:13px}
.filter svg{position:absolute;right:12px}
.close{position:absolute;right:28px;top:40px}
.group{position:absolute;left:56px}
.group-head{font-size:16px;display:flex;align-items:center;position:relative}
.group-head svg{position:absolute;left:-29px}
.group-words{margin-top:10px;font-size:15.5px;color:var(--modal-muted)}
.group-words.due{color:var(--accent-red)}
</style>
</head>
<body>
<aside class="sidebar">
  <svg class="avatar" width="88" height="88" viewBox="0 0 88 88"><circle cx="44" cy="44" r="40" fill="none" stroke="#6d737b" stroke-width="6"/><circle cx="44" cy="34" r="14" fill="#6d737b"/><path d="M20 68c4-14 14-18 24-18s20 4 24 18" fill="#6d737b"/></svg>
  <div class="user-name">Maren</div>
  <div class="user-mail">maren@quillvane-mail.org</div>
  <ul class="nav">
    <li class="nav-item"><svg width="26" height="20" viewBox="0 0 26 20"><path d="M13 1L1 11h4v8h6v-5h4v5h6v-8h4z" fill="#6d737b"/></svg>QuillVane</li>
    <li class="nav-item"><svg width="22" height="22" viewBox="0 0 22 22"><circle cx="11" cy="11" r="10" fill="#6d737b"/><text x="11" y="14" font-size="7" text-anchor="middle" fill="#151c27" font-family="Lato,sans-serif" font-weight="700">ENG</text></svg>Daily English</li>
    <li class="nav-item"><svg width="22" height="20" viewBox="0 0 22 20"><rect x="2" y="2" width="8" height="17" fill="#6d737b"/><rect x="11" y="8" width="8" height="11" fill="#6d737b"/></svg>Business</li>
    <li class="nav-item"><svg width="22" height="22" viewBox="0 0 22 22"><circle cx="11" cy="11" r="9" fill="none" stroke="#6d737b" stroke-width="2" stroke-dasharray="3 2"/><circle cx="11" cy="11" r="6" fill="#6d737b"/></svg>Short-Term Memory</li>
    <li class="nav-item active"><svg width="24" height="22" viewBox="0 0 24 22"><circle cx="10" cy="12" r="8" fill="#6d7ea0"/><circle cx="19" cy="5" r="3.5" fill="none" stroke="#6d7ea0" stroke-width="1.5"/></svg>Working Memory</li>
  </ul>
  <ul class="sub" style="position:absolute;top:370px;left:0">
    <li>Cool Down</li><li>Crave</li><li>Go For</li><li>Go-To</li><li>In The Mood For</li><li>Sip</li><li>Soothing</li><li>Stick With</li><li>Throw In/Throw On</li>
  </ul>
  <ul class="nav" style="top:578px">
    <li class="nav-item"><svg width="22" height="22" viewBox="0 0 22 22"><circle cx="11" cy="11" r="9" fill="none" stroke="#6d737b" stroke-width="2"/><circle cx="11" cy="11" r="5" fill="#6d737b"/></svg>Long-Term Memory</li>
  </ul>
</aside>

<header class="header">
  <div class="brand">QuillVane <svg width="16" height="10" viewBox="0 0 16 10" style="margin-left:10px"><path d="M1 1h14L8 9z" fill="#1b1b1b"/></svg></div>
  <div class="word-title">Grab <svg width="24" height="22" viewBox="0 0 24 22" style="vertical-align:-3px"><path d="M12 1l3.3 6.8 7.4 1-5.4 5.2 1.3 7.4L12 17.9l-6.6 3.5 1.3-7.4L1.3 8.8l7.4-1z" fill="var(--star)"/></svg></div>
  <svg style="position:absolute;right:12px;top:10px" width="26" height="20" viewBox="0 0 26 20"><path d="M1 2h24M1 10h24M1 18h24" stroke="#1b1b1b" stroke-width="2"/></svg>
</header>

<div class="card" style="left:284px;width:199px"></div>
<div class="card current" style="left:506px;width:201px"></div>
<div class="card" style="left:729px;width:199px"></div>
<div class="card" style="left:951px;width:201px"><span class="card-label">Reviews &nbsp;4</span><span class="card-bar"></span></div>

<p class="intro">The morning is busy and you're running late for class. You grab your bag and your keys on the way out of the door. As you reach the bus stop you realise that you forgot your coffee, and then your phone starts ringing in your pocket as the bus arrives.</p>
<div class="section-title" style="top:324px">Learning Curve</div>

<svg class="chart" width="1200" height="792" viewBox="0 0 1200 792" font-family="Lato,sans-serif" font-size="8" fill="#1b1b1b">
  <text x="295" y="404">Long-Term Memory</text>
  <text x="296" y="461">Working Memory</text>
  <text x="295" y="508">Short-Term Memory</text>
  <text x="295" y="527">Forgotten Memory</text>
  <rect x="375" y="504" width="17" height="34" fill="var(--bar)"/>
  <rect x="462" y="420" width="17" height="118" fill="var(--bar)"/>
  <rect x="355" y="479" width="40" height="18" fill="#999"/><text x="362" y="491">May 18</text>
  <rect x="429" y="410" width="40" height="18" fill="#999"/><text x="436" y="422">May 19</text>
  <path d="M393 504c20 2 40 10 70 34" fill="none" stroke="#1b1b1b" stroke-width="1.5" stroke-dasharray="1.5 3"/>
  <path d="M479 420c30 3 60 2 80 12s50 40 95 108" fill="none" stroke="#1b1b1b" stroke-width="1.5" stroke-dasharray="1.5 3"/>
  <line x1="293" y1="538" x2="1180" y2="538" stroke="#1b1b1b"/>
  <g stroke="#1b1b1b">
    <path d="M305 538v4M349 538v4M392 538v4M436 538v4M480 538v4M523 538v4M567 538v4M611 538v4M655 538v4M698 538v4M742 538v4M786 538v4M829 538v4M873 538v4M917 538v4M960 538v4M1004 538v4M1048 538v4M1091 538v4M1135 538v4M1179 538v4"/>
  </g>
  <g text-anchor="middle">
    <text x="309" y="555">18 May</text><text x="349" y="555">12:00</text>
    <text x="397" y="555">19 May</text><text x="436" y="555">12:00</text>
    <text x="485" y="555">20 May</text><text x="524" y="555">12:00</text>
    <text x="572" y="555">21 May</text><text x="611" y="555">12:00</text>
    <text x="659" y="555">22 May</text><text x="698" y="555">12:00</text>
    <text x="747" y="555">23 May</text><text x="786" y="555">12:00</text>
    <text x="834" y="555">24 May</text><text x="874" y="555">12:00</text>
    <text x="921" y="555">25 May</text><text x="961" y="555">12:00</text>
    <text x="1009" y="555">26 May</text><text x="1049" y="555">12:00</text>
    <text x="1096" y="555">27 May</text><text x="1136" y="555">12:00</text>
    <text x="1170" y="555">28 …</text>
  </g>
</svg>
<div class="axis-title">Date Range</div>

<div class="section-title" style="top:607px">QuillVane Learning Analysis</div>
<p class="analysis">Lorem ipsum dolor sit amet, consectetur adipiscing elit. Nam rutrum commodo enim id bibendum. Nunc dignissim risus erat, nec finibus nunc dictum eu. Aliquam sit amet euismod metus, quis malesuada erat. Sed at felis quis nulla feugiat cursus at at dolor. Maecenas pretium aliquet dapibus. Fusce et eleifend massa. Sed convallis ex mi, at lobortis ligula congue vel.</p>

<section class="modal" aria-label="Vocabulary by memory stage">
  <div class="filter">All<svg width="12" height="8" viewBox="0 0 12 8"><path d="M1 1l5 5 5-5" fill="none" stroke="#1f1f1f" stroke-width="1.5"/></svg></div>
  <svg class="close" width="14" height="14" viewBox="0 0 14 14"><path d="M1 1l12 12M13 1L1 13" stroke="#1f1f1f" stroke-width="1.6"/></svg>
  <div class="group" style="top:104px">
    <div class="group-head"><svg width="22" height="22" viewBox="0 0 22 22"><circle cx="11" cy="11" r="9.5" fill="none" stroke="#1f1f1f" stroke-width="1.4" stroke-dasharray="3 1.5"/><circle cx="11" cy="11" r="6.5" fill="#1f1f1f"/><path d="M11 7v4h3" stroke="#fff" stroke-width="1.3" fill="none"/></svg>Short-Term Memory</div>
    <div class="group-words due">Grab</div>
  </div>
  <div class="group" style="top:170px">
    <div class="group-head"><svg width="24" height="22" viewBox="0 0 24 22"><circle cx="10" cy="12" r="8" fill="#1f1f1f"/><circle cx="19" cy="5" r="3.5" fill="none" stroke="#1f1f1f" stroke-width="1.4"/></svg>Working Memory</div>
    <div class="group-words">Cool Down Crave Go For Go-To In The Mood For Sip Soothing Stick With Throw In/Throw On</div>
  </div>
  <div class="group" style="top:238px">
    <div class="group-head"><svg width="22" height="22" viewBox="0 0 22 22"><circle cx="11" cy="11" r="9.5" fill="none" stroke="#1f1f1f" stroke-width="1.4"/><circle cx="11" cy="11" r="6" fill="#1f1f1f"/><circle cx="11" cy="11" r="2.2" fill="#fff"/></svg>Long-Term Memory</div>
    <div class="group-words">Give It A Try</div>
  </div>
</section>
</body>
</html>
```